Harbor Grout Works Business card logo

We are a tile and natural stone installation company with an emphasis on high quality and design assistance. I prefer a black background with a graphic logo or maybe a photo that gives a feel of tile/natural stone. I like bold, but tasteful colors. Something to really catch the eye without being gaudy. The final design should convey expert quality and attention to detail.

Contact Information for Business Card

HARBOR GROUT WORKS Quality Design and Installation

Font styles to use
Other font styles liked:
• Graviton, Illegal curves

Requirements
Must have
• Business card must be an eye-catcher, but tasteful.
• Information I need on the card:
• Business name and tagline
• Dennis Halvorsen, owner
• Phone: (xxx) xxx-xxxx
• Email
• Website

```html
<!DOCTYPE html>
<html lang="en">
<head>
<meta charset="utf-8">
<title>Harbor Grout Works — Business Card</title>
<link rel="stylesheet" href="https://fonts.googleapis.com/css2?family=Michroma&family=Oswald:wght@400;500&display=swap">
<style>
  :root {
    --stage: #0b0b0c;
    --card-black: #050505;
    --gloss: #2a2a2c;
    --logo-silver: #d9d9d9;
    --text-light: #f2f2f2;
    --text-muted: #bdbdbd;
    --rule: #8a8a8a;
    --stone-light: #8e8d89;
    --stone-mid: #6f6e6a;
    --stone-dark: #4d4c49;
    --stone-ink: #3a3a38;
  }
  * { box-sizing: border-box; margin: 0; padding: 0; }
  html, body {
    width: 1200px; height: 871px; overflow: hidden;
    background: var(--stage);
  }
  .stage {
    width: 1200px; height: 871px;
    display: flex; flex-direction: column; align-items: center; justify-content: center;
    gap: 56px;
  }
  .card {
    width: 560px; height: 320px; position: relative; overflow: hidden;
    box-shadow: 0 14px 40px rgba(0,0,0,0.6);
  }

  /* Front */
  .card--front {
    background: linear-gradient(120deg, var(--gloss) 0%, #151516 38%, var(--card-black) 62%);
    display: flex; align-items: center; padding: 0 28px;
  }
  .front-logo { width: 262px; }
  .wordmark {
    font-family: "Michroma", sans-serif; font-weight: 400;
    color: var(--logo-silver); font-size: 25px; line-height: 1.15; letter-spacing: 1px;
  }
  .tagline {
    font-family: "Michroma", sans-serif; font-size: 7.6px; letter-spacing: 1.4px;
    color: var(--logo-silver); text-transform: uppercase; margin-top: 8px;
  }
  .divider { width: 1px; height: 124px; background: var(--rule); margin: 0 18px 0 12px; }
  .contact { color: var(--text-light); }
  .contact__name {
    font-family: "Michroma", sans-serif; font-size: 13px; letter-spacing: 2.5px;
    text-transform: uppercase; font-variant: small-caps;
  }
  .contact__role {
    font-family: "Michroma", sans-serif; font-size: 8px; letter-spacing: 2px;
    color: var(--text-muted); text-transform: uppercase; margin: 2px 0 10px;
  }
  .contact__row {
    display: flex; align-items: center; gap: 8px;
    font-family: "Oswald", sans-serif; font-weight: 500; font-size: 13px; letter-spacing: 0.4px;
    margin-bottom: 6px;
  }
  .contact__row svg { width: 11px; height: 11px; flex: none; }

  /* Back */
  .card--back { display: flex; align-items: center; justify-content: center; }
  .stone {
    position: absolute; inset: 0;
    background:
      radial-gradient(ellipse at 25% 30%, var(--stone-light) 0%, transparent 55%),
      radial-gradient(ellipse at 80% 75%, var(--stone-dark) 0%, transparent 60%),
      linear-gradient(135deg, var(--stone-mid), var(--stone-dark));
  }
  .back-logo { position: relative; text-align: center; }
  .back-logo .wordmark { color: var(--stone-ink); font-size: 40px; line-height: 1.1; letter-spacing: 2px; }
  .back-logo .tagline { color: var(--stone-ink); font-size: 10px; letter-spacing: 2px; margin-top: 10px; }
</style>
</head>
<body>
<main class="stage">
  <section class="card card--front" aria-label="Business card front">
    <div class="front-logo">
      <div class="wordmark">HARBOR<br>GROUT WORKS</div>
      <div class="tagline">Quality Design and Installation</div>
    </div>
    <div class="divider"></div>
    <div class="contact">
      <div class="contact__name">Dennis Halvorsen</div>
      <div class="contact__role">Owner</div>
      <div class="contact__row">
        <svg viewBox="0 0 24 24" fill="var(--text-light)"><path d="M6.6 10.8a15 15 0 0 0 6.6 6.6l2.2-2.2a1 1 0 0 1 1-.25 11.4 11.4 0 0 0 3.6.57 1 1 0 0 1 1 1V20a1 1 0 0 1-1 1A17 17 0 0 1 3 4a1 1 0 0 1 1-1h3.5a1 1 0 0 1 1 1c0 1.25.2 2.45.57 3.57a1 1 0 0 1-.25 1z"/></svg>
        (555) 014-2290
      </div>
      <div class="contact__row">
        <svg viewBox="0 0 24 24" fill="none" stroke="var(--text-light)" stroke-width="2"><rect x="2" y="5" width="20" height="14"/><path d="M2 5l10 8 10-8"/></svg>
        hello@harborgroutworks.com
      </div>
      <div class="contact__row">
        <svg viewBox="0 0 24 24" fill="none" stroke="var(--text-light)" stroke-width="2"><circle cx="12" cy="12" r="10"/><path d="M2 12h20M12 2c3 3 3 17 0 20M12 2c-3 3-3 17 0 20"/></svg>
        www.harborgroutworks.com
      </div>
    </div>
  </section>

  <section class="card card--back" aria-label="Business card back">
    <div class="stone" role="img" aria-label="Grey natural stone texture background"></div>
    <div class="back-logo">
      <div class="wordmark">HARBOR<br>GROUT WORKS</div>
      <div class="tagline">Quality Design and Installation</div>
    </div>
  </section>
</main>
</body>
</html>
```